Tallowmere Air Business Card Design

Design new, 2 sides, business cards for a residential and light commercial heating, air conditioning contractor.

Target Market(s)

Homeowners, small businesses

Industry/Entity Type

Business

Contact Information for Business Card

Dominic Westerhall
Phone - 862-415-2736
Email
Address - PO box 518
Brightwater NJ 07912
Website - www.HarborBreezeLLC.example

Requirements
Must have
• logo, company colors, standard size with no die cut, so I can use nova stamp

```html
<!DOCTYPE html>
<html lang="en">
<head>
<meta charset="utf-8">
<title>Tallowmere Air Business Card</title>
<link rel="stylesheet" href="https://fonts.googleapis.com/css2?family=Open+Sans:wght@400;600;700&display=swap">
<style>
  :root {
    --backdrop: #e9e6e1;
    --front-bg: #0f0f0f;
    --back-bg: #58585a;
    --band-dark: #3c3c3e;
    --cell-darker: #2c2c2e;
    --cell-mid: #37373a;
    --text-light: #ffffff;
    --text-soft: #e6e6e6;
    --brand-cream: #f6e3c4;
  }
  * { box-sizing: border-box; margin: 0; padding: 0; }
  html, body { width: 1200px; height: 900px; overflow: hidden; }
  body {
    background: var(--backdrop);
    font-family: "Open Sans", Arial, sans-serif;
    position: relative;
  }
  .card {
    position: absolute;
    left: 280px;
    width: 640px;
    height: 366px;
    box-shadow: 0 6px 18px rgba(0,0,0,.18);
    overflow: hidden;
  }
  .card--front { top: 64px; background: var(--front-bg); }
  .card--back { top: 470px; background: var(--back-bg); }

  .brand-name {
    position: absolute;
    left: 0; right: 0;
    text-align: center;
    font-weight: 700;
    text-transform: uppercase;
    letter-spacing: 3px;
    white-space: nowrap;
  }
  .card--front .brand-name { top: 120px; font-size: 46px; color: var(--brand-cream); }
  .card--back .brand-name { top: 58px; font-size: 34px; color: var(--text-light); }

  .front-url {
    position: absolute;
    left: 0; right: 0; bottom: 40px;
    text-align: center;
    color: var(--text-soft);
    font-size: 15px;
  }

  .person {
    position: absolute;
    left: 0; right: 0; top: 128px;
    text-align: center;
    color: var(--text-light);
  }
  .person__name { font-size: 21px; font-weight: 700; }
  .person__title { font-size: 20px; font-weight: 400; line-height: 1.1; }

  .contact-row {
    position: absolute;
    left: 0; right: 0; top: 210px;
    height: 44px;
    background: var(--band-dark);
    display: flex;
  }
  .contact-cell {
    display: flex;
    align-items: center;
    gap: 8px;
    color: var(--text-light);
    padding: 0 14px;
    white-space: nowrap;
  }
  .contact-cell svg { width: 14px; height: 14px; fill: var(--text-light); flex: none; }
  .contact-cell--phone { background: var(--cell-darker); width: 200px; font-size: 18px; justify-content: center; }
  .contact-cell--email { background: var(--cell-mid); width: 240px; font-size: 14px; justify-content: center; }
  .contact-cell--mobile { width: 200px; font-size: 14px; justify-content: center; }

  .address {
    position: absolute;
    left: 0; right: 0; top: 254px;
    height: 50px;
    display: flex; align-items: center; justify-content: center;
    color: var(--text-soft);
    font-size: 17px;
  }
</style>
</head>
<body>
  <section class="card card--front">
    <div class="brand-name">Tallowmere Air</div>
    <div class="front-url">www.TallowmereAirLLC.example</div>
  </section>

  <section class="card card--back">
    <div class="brand-name">Tallowmere Air</div>
    <div class="person">
      <div class="person__name">Dominic Westerhall</div>
      <div class="person__title">Director</div>
    </div>
    <div class="contact-row">
      <div class="contact-cell contact-cell--phone">
        <svg viewBox="0 0 16 16" aria-hidden="true"><path d="M2 5c0-2 2-3 6-3s6 1 6 3v1h-3V5H5v1H2z"/><path d="M4 8h8l2 6H2z"/></svg>
        <span>862-415-2736</span>
      </div>
      <div class="contact-cell contact-cell--email">
        <svg viewBox="0 0 16 16" aria-hidden="true"><path d="M1 3h14v10H1z M2 4l6 5 6-5" fill="none" stroke="#fff" stroke-width="1.5"/></svg>
        <span>info@tallowmereair.example</span>
      </div>
      <div class="contact-cell contact-cell--mobile">
        <svg viewBox="0 0 16 16" aria-hidden="true"><path d="M4 1h8v14H4z M5.5 3h5v9h-5z" fill-rule="evenodd"/></svg>
        <span>862-415-2790</span>
      </div>
    </div>
    <div class="address">PO box 518 Brightwater NJ 07912</div>
  </section>
</body>
</html>
```